Request for Business Card Design

Hi. My name is Marlene, I am looking for a new business card design for my company, Quarrow Signal Instruments, LLC. I really like the design you did for Tarsel Venture and was hoping you could do something similar using our full logo and our mark. I am also open to any raised texture design using our mark. I have attached our full logo, which would need to be somewhere on the card, as well as the mark in both outline and full form, as well as our brand colors / guide. The card does not have to be white, as long as our logo and mark appear. I actually like darker colored business cards more, but am open to all options. If you are interested in working with me, please let me know. We would also take the business card design into letterhead design if you can do that.

```html
<!DOCTYPE html>
<html lang="en">
<head>
<meta charset="utf-8">
<title>Quarrow Signal Instruments – Business Card</title>
<link rel="stylesheet" href="https://fonts.googleapis.com/css2?family=Arimo:ital,wght@0,400;0,700;1,400;1,700&display=swap">
<style>
  :root {
    --stage: #0e0e0e;
    --card: #232323;
    --card-edge: #0a8ab3;
    --accent: #0b8fba;
    --ink: #f2f2f2;
    --ink-soft: #d9d9d9;
    --rule: #cfcfcf;
    --emboss: #2b2b2b;
    --emboss-shadow: #161616;
  }
  * { box-sizing: border-box; margin: 0; padding: 0; }
  html, body {
    width: 1200px; height: 963px; overflow: hidden;
    background: var(--stage);
    font-family: "Arimo", Arial, sans-serif;
  }
  .sheet {
    width: 1200px; height: 963px;
    display: flex; flex-direction: column;
    align-items: center; justify-content: center; gap: 50px;
  }
  .card {
    position: relative;
    width: 700px; height: 400px;
    background: var(--card);
    border-radius: 26px;
    box-shadow: 0 5px 0 var(--card-edge), 0 18px 40px rgba(0,0,0,.6);
    overflow: hidden;
  }

  /* front */
  .card-front { display: flex; align-items: center; }
  .brand { width: 360px; padding-left: 56px; }
  .brand-lockup { display: flex; align-items: center; gap: 16px; }
  .brand-dot {
    width: 46px; height: 46px; border-radius: 50%;
    background: var(--accent); flex: none;
  }
  .brand-name {
    color: var(--ink); font-weight: 700; font-size: 38px;
    letter-spacing: 4px; line-height: 1;
  }
  .brand-sub {
    color: var(--ink); font-weight: 700; font-size: 12.5px;
    letter-spacing: 2.6px; line-height: 1; margin-top: 8px;
  }
  .divider { width: 1px; height: 230px; background: var(--rule); }
  .contact { padding-left: 34px; font-style: italic; }
  .person-name {
    color: var(--accent); font-weight: 700; font-size: 27px;
    letter-spacing: 1px; text-transform: uppercase;
  }
  .person-role { color: var(--ink-soft); font-size: 19px; margin-top: 2px; }
  .address { color: var(--ink-soft); font-size: 19px; line-height: 1.3; margin-top: 22px; }
  .details { list-style: none; margin-top: 18px; }
  .details li {
    display: flex; align-items: center; gap: 12px;
    color: var(--ink-soft); font-size: 19px; line-height: 1.55;
  }
  .details svg { width: 17px; height: 17px; flex: none; }

  /* back */
  .card-back { display: flex; align-items: center; justify-content: center; gap: 22px; }
  .emboss-dot {
    width: 120px; height: 120px; border-radius: 50%;
    background: var(--card);
    box-shadow: inset 3px 3px 6px var(--emboss-shadow), inset -2px -2px 4px #333;
  }
  .emboss-name {
    color: var(--emboss); font-weight: 700; font-size: 46px; letter-spacing: 5px;
    text-shadow: 1px 1px 0 #333, -1px -1px 0 var(--emboss-shadow);
  }
</style>
</head>
<body>
<main class="sheet">
  <section class="card card-front" aria-label="Business card front">
    <div class="brand">
      <div class="brand-lockup">
        <span class="brand-dot"></span>
        <div>
          <div class="brand-name">QUARROW</div>
          <div class="brand-sub">SIGNAL INSTRUMENTS</div>
        </div>
      </div>
    </div>
    <div class="divider"></div>
    <div class="contact">
      <h1 class="person-name">Edwin Harlow</h1>
      <p class="person-role">Manager</p>
      <p class="address">Your Address, City<br>State, Zip 0000</p>
      <ul class="details">
        <li>
          <svg viewBox="0 0 24 24" fill="var(--accent)"><path d="M6.6 10.8a15 15 0 0 0 6.6 6.6l2.2-2.2a1 1 0 0 1 1-.25 11.4 11.4 0 0 0 3.6.57 1 1 0 0 1 1 1V20a1 1 0 0 1-1 1A17 17 0 0 1 3 4a1 1 0 0 1 1-1h3.5a1 1 0 0 1 1 1c0 1.25.2 2.45.57 3.57a1 1 0 0 1-.25 1z"/></svg>
          123-456-2100
        </li>
        <li>
          <svg viewBox="0 0 24 24" fill="none" stroke="var(--accent)" stroke-width="2"><rect x="3" y="5" width="18" height="14" rx="1"/><path d="M3 6l9 7 9-7"/></svg>
          youremail@quarrowmail.com
        </li>
        <li>
          <svg viewBox="0 0 24 24" fill="none" stroke="var(--accent)" stroke-width="1.8"><circle cx="12" cy="12" r="9"/><path d="M3 12h18M12 3c3 3 3 15 0 18M12 3c-3 3-3 15 0 18"/></svg>
          www.yourwebsite.com
        </li>
      </ul>
    </div>
  </section>

  <section class="card card-back" aria-label="Business card back">
    <span class="emboss-dot"></span>
    <span class="emboss-name">QUARROW</span>
  </section>
</main>
</body>
</html>
```